BRIGHT RIVER POWER.

I'd like my business logo.
contact name: Dennis Halvorsen
phone:0438759164
email: info@brightriverpower.net.au
website: www.brightriverpower.net.au

services:
solar
battery storage
LED lighting
energy saving solutions
general electrical
I'd like the design to look professional

Target Market(s)

Everyone

Industry/Entity Type

Business

Contact Information for Business Card

as described above

Requirements
Must have
• Id like the colours and the design to work well with my logo.

```html
<!DOCTYPE html>
<html lang="en">
<head>
<meta charset="utf-8">
<title>Bright River Power – Business Card</title>
<link href="https://fonts.googleapis.com/css2?family=Open+Sans:wght@400;600;700&display=swap" rel="stylesheet">
<style>
  :root {
    --backdrop: #3b3531;
    --card: #0d0d0d;
    --orange: #f5a21b;
    --green: #7cc43a;
    --white: #f2f2f2;
  }
  * { box-sizing: border-box; margin: 0; padding: 0; }
  html, body {
    width: 1200px; height: 844px; overflow: hidden;
    background: var(--backdrop);
    font-family: "Open Sans", Arial, sans-serif;
  }
  .stage { position: relative; width: 1200px; height: 844px; }
  .card {
    position: absolute; top: 268px;
    width: 540px; height: 308px;
    background: var(--card);
    border-radius: 3px;
    box-shadow: 0 10px 30px rgba(0,0,0,.45);
    overflow: hidden;
  }
  .card--front { left: 36px; }
  .card--back { left: 624px; }

  .brand { display: flex; align-items: center; gap: 12px; }
  .brand__dot { width: 40px; height: 40px; border-radius: 50%; background: var(--orange); flex: none; }
  .brand__name { color: var(--green); font-weight: 700; font-size: 24px; letter-spacing: .5px; line-height: 1; }

  .card--front .brand { position: absolute; left: 40px; top: 78px; }
  .divider { position: absolute; height: 1px; background: var(--orange); }
  .card--front .divider { left: 0; top: 160px; width: 330px; }
  .contact-name {
    position: absolute; right: 40px; top: 146px;
    color: var(--orange); font-weight: 600; font-size: 19px;
  }
  .contact-list {
    position: absolute; right: 40px; top: 186px;
    list-style: none; text-align: right;
    color: var(--white); font-size: 14px; line-height: 25px;
  }
  .contact-list li { display: flex; justify-content: flex-end; align-items: center; gap: 8px; }
  .contact-list svg { width: 12px; height: 12px; fill: var(--orange); flex: none; }

  .card--back .brand { position: absolute; left: 0; right: 0; top: 64px; justify-content: center; }
  .card--back .divider { top: 160px; width: 190px; }
  .card--back .divider--left { left: 0; }
  .card--back .divider--right { right: 0; }
  .services-title {
    position: absolute; left: 0; right: 0; top: 149px; text-align: center;
    color: var(--orange); font-weight: 600; font-size: 17px;
  }
  .services {
    position: absolute; left: 0; right: 0; top: 188px; text-align: center;
    color: var(--white); font-size: 14px; line-height: 24px;
  }
  .services__bullet {
    display: inline-block; width: 8px; height: 8px; border-radius: 50%;
    background: var(--green); margin: 0 6px; vertical-align: middle;
  }
</style>
</head>
<body>
<main class="stage">
  <section class="card card--front" aria-label="Business card front">
    <div class="brand">
      <span class="brand__dot"></span>
      <span class="brand__name">BRIGHT RIVER POWER</span>
    </div>
    <div class="divider"></div>
    <p class="contact-name">Dennis Halvorsen</p>
    <ul class="contact-list">
      <li>0438759164
        <svg viewBox="0 0 24 24" aria-hidden="true"><path d="M6.6 10.8a15.1 15.1 0 0 0 6.6 6.6l2.2-2.2a1 1 0 0 1 1-.25 11.4 11.4 0 0 0 3.6.57 1 1 0 0 1 1 1V20a1 1 0 0 1-1 1A17 17 0 0 1 3 4a1 1 0 0 1 1-1h3.5a1 1 0 0 1 1 1c0 1.25.2 2.45.57 3.57a1 1 0 0 1-.25 1z"/></svg>
      </li>
      <li>info@brightriverpower.net.au
        <svg viewBox="0 0 24 24" aria-hidden="true"><path d="M2 5h20v14H2z M2 5l10 8 10-8" fill="var(--orange)"/><path d="M3 6l9 7 9-7" fill="none" stroke="#0d0d0d" stroke-width="2"/></svg>
      </li>
      <li>www.brightriverpower.net.au
        <svg viewBox="0 0 24 24" aria-hidden="true"><circle cx="12" cy="12" r="10"/><path d="M2 12h20M12 2c3 3 3 17 0 20M12 2c-3 3-3 17 0 20" fill="none" stroke="#0d0d0d" stroke-width="1.6"/></svg>
      </li>
    </ul>
  </section>

  <section class="card card--back" aria-label="Business card back">
    <div class="brand">
      <span class="brand__dot"></span>
      <span class="brand__name">BRIGHT RIVER POWER</span>
    </div>
    <div class="divider divider--left"></div>
    <p class="services-title">What I do</p>
    <div class="divider divider--right"></div>
    <p class="services">
      Solar<span class="services__bullet"></span>Battery Storage<span class="services__bullet"></span>LED Lighting<br>
      Energy Saving Solutions
    </p>
  </section>
</main>
</body>
</html>
```